Torvane Halbridge

Looking for modern business cards.
Clean contemporary design.
Similar to this.
https://www.plumvexa-search.example/imgres?imgurl=https%3A%2F%2Fimg.quorlint-cdn.example%2Fsleek_dark_metal_card_design_540.jpg&imgrefurl=https%3A%2F%2Fwww.quorlint-prints.example%2Fsleek_dark_metal_card_design-918273645501928374&q=modern%20business%20cards

But I'd like the blue to look metallic.

Business

```html
<!DOCTYPE html>
<html lang="en">
<head>
<meta charset="utf-8">
<title>Torvane Halbridge — Business Card</title>
<link rel="stylesheet" href="https://fonts.googleapis.com/css2?family=Lato:wght@400;700&display=swap">
<style>
  :root {
    --stage: #1d1d1d;
    --card-core: #2b2b2b;
    --card-edge: #0e0e0e;
    --steel-light: #3d7592;
    --steel-mid: #25586f;
    --steel-dark: #1a4257;
    --ink: #ffffff;
    --ink-soft: #e6e6e6;
    --accent: #1e9fd0;
  }
  * { box-sizing: border-box; margin: 0; padding: 0; }
  html, body {
    width: 1200px; height: 900px; overflow: hidden;
    background: var(--stage);
    font-family: "Lato", Arial, sans-serif;
  }
  .canvas { position: relative; width: 1200px; height: 900px; }
  .card {
    position: absolute; top: 307px; width: 440px; height: 271px; overflow: hidden;
    background: radial-gradient(ellipse 70% 80% at 50% 30%, var(--card-core), var(--card-edge));
    box-shadow: 0 4px 10px rgba(0,0,0,.6);
  }
  .card--front { left: 149px; }
  .card--back { left: 609px; }

  .steel-band { position: absolute; inset: 0; width: 100%; height: 100%; }

  .identity { position: absolute; left: 24px; top: 37px; color: var(--ink); }
  .identity__name { font-size: 16px; font-weight: 700; letter-spacing: .2px; text-transform: uppercase; line-height: 19px; }
  .identity__title { font-size: 13px; color: var(--ink-soft); line-height: 16px; }

  .contacts { position: absolute; left: 24px; top: 134px; list-style: none; color: var(--ink); font-size: 13px; line-height: 16px; }
  .contacts li { display: flex; align-items: center; gap: 4px; }
  .contacts svg { width: 11px; height: 11px; fill: var(--ink); }

  .address { position: absolute; right: 29px; top: 212px; text-align: right; color: var(--ink); font-size: 13px; line-height: 16px; }

  .brand { position: absolute; left: 0; right: 0; top: 132px; display: flex; justify-content: center; align-items: center; gap: 10px; }
  .brand__dot { width: 12px; height: 12px; border-radius: 50%; background: var(--accent); }
  .brand__name { font-size: 26px; font-weight: 400; color: var(--accent); line-height: 1; }

  .site { position: absolute; left: 0; right: 0; top: 224px; text-align: center; font-size: 12px; font-weight: 700; letter-spacing: 1.6px; color: var(--accent); }
</style>
</head>
<body>
<main class="canvas">
  <section class="card card--front" aria-label="Card front">
    <svg class="steel-band" viewBox="0 0 440 271" preserveAspectRatio="none" aria-hidden="true">
      <defs>
        <linearGradient id="steel" x1="0" y1="1" x2="1" y2="0">
          <stop offset="0" stop-color="var(--steel-dark)"/>
          <stop offset=".45" stop-color="var(--steel-mid)"/>
          <stop offset=".7" stop-color="var(--steel-light)"/>
          <stop offset="1" stop-color="var(--steel-mid)"/>
        </linearGradient>
      </defs>
      <path d="M0,250 Q270,215 440,76 L440,271 L0,271 Z" fill="url(#steel)"/>
    </svg>
    <div class="identity">
      <p class="identity__name">Marek Ellsworth</p>
      <p class="identity__title">Managing Director</p>
    </div>
    <ul class="contacts">
      <li><svg viewBox="0 0 12 12"><path d="M1 4c0-2 2-3 3-3l1 2-1 1c0 2 2 4 4 4l1-1 2 1c0 1-1 3-3 3C4 11 1 8 1 4z"/></svg>444 555 0192</li>
      <li><svg viewBox="0 0 12 12"><path d="M1 3h10v6H1z M1 3l5 4 5-4" stroke="#222" stroke-width=".8"/></svg>info@halbridgemail.com</li>
      <li><svg viewBox="0 0 12 12"><circle cx="6" cy="6" r="5"/><path d="M3 4h3v2H4z M7 7h2v2H7z" fill="#222"/></svg>www.halbridgeadvisory.com</li>
    </ul>
    <address class="address" style="font-style:normal">421, Address line here<br>Country Name,45452</address>
  </section>

  <section class="card card--back" aria-label="Card back">
    <div class="brand">
      <span class="brand__dot"></span>
      <span class="brand__name">Torvane Halbridge</span>
    </div>
    <p class="site">www.torvane.com</p>
  </section>
</main>
</body>
</html>
```